Tech Website

1. Overview
Prism48, formally named LumoVista, is a pioneer in computer vision technology and machine learning. Based out of Santa Clara, California, Prism48 is at the forefront of the User Interface revolution; building technology architecture that grants devices with the aptitude to respond to emotional detection, gaze tracking, facial recognition, age and gender identification and gaming interaction. Winner of the Mobile Track at NOVA Founders Sprint 2012, Prism48 has developed the next generation of consumer behaviour analytics. Prism48 software solutions are scalable across various platforms including mobile phone, tablets, PC and SmartTV.
Updates

Good day, 

Please see the update to our brief - there is a PDF of the type of format and design we are looking for.  It shows each page - Landing, Technology, Product, Press and Company.

Thank you for your designs

Regards,

Target Market(s)

Target market - A mix of enterprise and consumer audiences, targeting the need for the technology in the living room space

Industry/Entity Type

Architecture

Requirements
Must have
• Design preferences - Easy to navigate, modern with sleek feel, trendy, tech saavy, using cube as a consistent element/theme. colours are not determined, but parrot green was one idea with 2 additional underlying colours. keys words like user interface revolution or sense recognition are good sources to draw inspiration.

Landing page will have a video - illustrating different uses of technology

Technical Specs - Landing page, 6 tabs/subpages, and each subpage may have 1 or 2 additional pages. Coding will be necessary, not that much at the beginning stages.

```html
<!DOCTYPE html>
<html lang="en">
<head>
<meta charset="utf-8">
<title>Prism48 – Home</title>
<link href="https://fonts.googleapis.com/css2?family=Exo:wght@400;500&family=Arimo:wght@400;700&display=swap" rel="stylesheet">
<style>
:root{
  --green:#6cc92f;
  --green-dark:#3f9a16;
  --ink:#222;
  --body:#444;
  --muted:#888;
  --band:#efefef;
  --line:#d8d8d8;
  --footer:#1b1b1b;
  --footer-text:#e6e6e6;
  --maroon:#8a1c1c;
}
*{box-sizing:border-box;margin:0;padding:0}
html,body{width:825px;height:1200px;overflow:hidden;background:#fff}
body{font-family:"Arimo",Arial,sans-serif;color:var(--body)}
.page{position:relative;width:825px;height:1200px;overflow:hidden;
  background:linear-gradient(#f3f3f3 0,#fff 160px,#fff 100%)}
.abs{position:absolute}
.top-bar{left:0;top:0;width:825px;height:6px;background:var(--green)}
.brand{left:86px;top:18px;font-family:"Exo",sans-serif;font-size:28px;font-weight:400;color:var(--ink);line-height:32px}
.search{left:552px;top:30px;width:182px;height:19px;background:#fff;border-radius:3px;
  box-shadow:0 4px 6px rgba(0,0,0,.12);font-size:10px;color:#999;padding:3px 8px}
.search svg{position:absolute;right:4px;top:2px}
.nav{top:84px;height:26px;font-family:"Exo",sans-serif;font-size:14px;color:#333;line-height:26px}
.nav-home{left:288px;width:66px;background:var(--green);color:#fff;text-align:center}
.hero-visual{left:69px;top:150px;width:575px;height:235px;
  background:linear-gradient(100deg,#f6f6f6 0%,#e8d2c2 18%,#f4f4f4 40%,#dcdcdc 70%,#fbfbfb 100%);
  border-bottom:1px solid #eee}
.hero-title{left:374px;top:158px;font-family:"Exo",sans-serif;font-size:30px;line-height:39px;color:var(--green)}
.hero-title .sub{color:#666}
.hero-arrows{left:653px;top:334px}
.welcome-title{left:90px;top:428px;font-size:16.5px;color:var(--ink)}
.welcome-text{left:90px;top:456px;width:347px;font-size:8.2px;line-height:16.5px;text-align:justify;color:#444}
.video{left:446px;top:430px;width:290px;height:187px}
.video-frame{position:absolute;inset:0 0 25px 0;
  background:linear-gradient(120deg,#f0f0f0 0%,#d6d6d6 35%,#6e5a55 55%,#9fb6c6 75%,#3aa7e6 100%)}
.video-bar{position:absolute;left:0;bottom:0;width:290px;height:25px;background:#222}
.btn-more{left:370px;top:646px;width:64px;height:21px;background:#e6e6e6;font-size:8.5px;color:#777;
  text-align:center;line-height:21px}
.band{left:0;top:676px;width:825px;height:370px;background:linear-gradient(#e9e9e9,#f6f6f6 60px,#f6f6f6)}
.sec-title{top:703px;font-size:16.5px;color:var(--ink)}
.quote-mark{font-family:Georgia,serif;font-size:20px;color:#bbb}
.testimonial{left:99px;top:746px;width:180px;font-size:9px;line-height:12.4px;text-align:justify;color:#222}
.testimonial-by{left:170px;top:844px;font-size:9.5px;color:var(--maroon)}
.link-more{font-size:8.5px;color:#777}
.thumb{background:#fff;border:1px solid #ddd;padding:5px;box-shadow:0 1px 2px rgba(0,0,0,.08)}
.thumb i{display:block;width:100%;height:100%;background:linear-gradient(135deg,#d9c0a8,#8a6a4e)}
.blog-card{left:314px;top:808px;width:114px;height:72px;background:rgba(255,255,255,.94);
  box-shadow:0 1px 4px rgba(0,0,0,.15);padding:5px 5px;font-size:7px;line-height:9px;color:#555;text-align:justify}
.blog-card .date{display:block;text-align:right;margin-top:3px}
.tech-item{left:528px;width:200px;height:75px}
.tech-item .thumb{position:absolute;left:0;top:0;width:62px;height:72px}
.tech-item p{position:absolute;left:68px;top:0;width:129px;font-size:7.8px;line-height:12.3px;text-align:justify;color:#444}
.alliance{left:101px;top:946px;width:618px;height:79px;background:#fff;border:1px solid #ccc;border-radius:2px}
.alliance h3{text-align:center;font-size:9.5px;letter-spacing:.6px;color:#222;margin-top:9px;padding-bottom:5px;
  border-bottom:1px dashed #ccc;margin-left:6px;margin-right:6px}
.partners{display:flex;justify-content:space-around;align-items:center;height:48px;padding:0 6px}
.partners span{font-size:13px;font-weight:700;color:#666}
.footer{left:0;top:1046px;width:825px;height:154px;background:var(--footer);color:var(--footer-text)}
.footer h4{position:absolute;font-weight:400;font-size:12px;font-family:"Arimo",sans-serif}
.sitemap{position:absolute;left:75px;top:51px;list-style:none;font-size:8.8px;line-height:15.8px}
.social{position:absolute;left:210px;top:60px;display:flex;gap:5px}
.social i{display:block;width:16px;height:16px;background:#eee;border-radius:3px}
.contact{position:absolute;left:399px;top:54px;font-size:8.3px;line-height:16.5px}
.map{position:absolute;left:554px;top:40px;width:186px;height:71px;background:linear-gradient(135deg,#e9e6dc,#d9d7ce);border:2px solid #fff}
.copy{position:absolute;right:98px;top:133px;font-size:7.5px;color:#ccc}
</style>
</head>
<body>
<div class="page">
  <div class="abs top-bar"></div>

  <div class="abs brand">Prism48</div>

  <div class="abs search">Search
    <svg width="16" height="16" viewBox="0 0 16 16"><circle cx="6.5" cy="6.5" r="4.5" fill="none" stroke="#888" stroke-width="1.6"/><line x1="10" y1="10" x2="14" y2="14" stroke="#888" stroke-width="2"/></svg>
  </div>

  <nav>
    <div class="abs nav nav-home">Home</div>
    <div class="abs nav" style="left:382px">About Us</div>
    <div class="abs nav" style="left:481px">Press</div>
    <div class="abs nav" style="left:551px">Technology</div>
    <div class="abs nav" style="left:665px">Contact Us</div>
  </nav>

  <div class="abs hero-visual" role="img" aria-label="Hand tapping a white tablet lying flat"></div>
  <h1 class="abs hero-title" style="font-weight:400">Allows mobile<br>applications to leverage<br><span class="sub">front facing camera</span></h1>
  <svg class="abs hero-arrows" width="60" height="26" viewBox="0 0 60 26">
    <circle cx="13" cy="13" r="12.5" fill="#777"/><polygon points="16,7 8,13 16,19" fill="#fff"/>
    <circle cx="45" cy="13" r="12.5" fill="#777"/><polygon points="42,7 50,13 42,19" fill="#fff"/>
  </svg>

  <h2 class="abs welcome-title" style="font-weight:400">Welcome to our Website</h2>
  <p class="abs welcome-text">Sed ut perspiciatis unde omnis iste natus error sit voluptatem accusantium doloremque laudantium, totam rem aperiam, eaque ipsa quae ab illo inventore veritatis et quasi architecto beatae vitae dicta sunt explicabo. Nemo enim ipsam voluptatem quia voluptas sit aspernatur aut odit aut fugit, sed quia consequuntur magni dolores eos qui ratione voluptatem sequi nesciunt. Neque porro quisquam est, qui dolorem ipsum quia dolor sit amet, consectetur, adipisci velit, sed quia non numquamSed ut perspiciatis unde omnis iste natus error sit voluptatem accusantium doloremque laudantium, totam rem aperiam, eaque ipsa quae ab illo inventore veritatis et quasi architecto beatae vitae dicta sunt explicabo. Nemo enim ipsam voluptatem quia voluptas sit aspernatur aut odit aut fugit, sed quia consequuntur magni dolores eos qui ratione voluptatem sequi nesciunt. Neque porro quisquam est, qui dolorem ipsum quia dolor sit amet, consectetur, adipisci velit, sed quia non numquam</p>

  <div class="abs video">
    <div class="video-frame" role="img" aria-label="Video still of a video call on a tablet with a blue cover"></div>
    <svg style="position:absolute;left:125px;top:64px" width="52" height="52" viewBox="0 0 52 52"><circle cx="26" cy="26" r="25" fill="rgba(0,0,0,.65)"/><polygon points="21,16 37,26 21,36" fill="#fff"/></svg>
    <div class="video-bar">
      <svg width="290" height="25" viewBox="0 0 290 25">
        <polygon points="12,7 21,12.5 12,18" fill="#fff"/>
        <rect x="32" y="11" width="198" height="3" fill="#fff"/><rect x="32" y="11" width="28" height="3" fill="#888"/>
        <polygon points="243,10 247,10 251,6 251,19 247,15 243,15" fill="#bbb"/>
        <path d="M254 9 q3 3.5 0 7" stroke="#bbb" fill="none"/>
        <path d="M267 6 l12 13 M279 6 l-12 13" stroke="#bbb" stroke-width="1.5"/>
      </svg>
    </div>
  </div>

  <div class="abs btn-more">Read more...</div>

  <div class="abs band"></div>

  <h2 class="abs sec-title" style="left:99px;font-weight:400">Testimonials</h2>
  <h2 class="abs sec-title" style="left:312px;font-weight:400">Blog</h2>
  <h2 class="abs sec-title" style="left:533px;font-weight:400">Technology Uses</h2>

  <div class="abs quote-mark" style="left:98px;top:724px">&ldquo;</div>
  <p class="abs testimonial">Lorem ipsum dolor sit amet, consectetur adipisicing elit, sed do eiusmod tempor incididunt ut labore et dolore magna aliqua. Ut enim ad minim veniam, quis nostrud exercitation ullamco laboris nisi ut aliquip.Lorem ipsum dolor sit amet, consectetur adipisicing</p>
  <div class="abs testimonial-by">-Ravina / 22-jun-2012</div>
  <div class="abs quote-mark" style="left:266px;top:856px">&rdquo;</div>
  <div class="abs link-more" style="left:227px;top:907px">Read more...</div>

  <div class="abs thumb" style="left:310px;top:738px;width:92px;height:76px"><i role="img" aria-label="Blog author portrait"></i></div>
  <div class="abs thumb" style="left:419px;top:738px;width:92px;height:76px"><i role="img" aria-label="Blog author portrait"></i></div>
  <div class="abs thumb" style="left:310px;top:822px;width:92px;height:76px"><i role="img" aria-label="Blog author portrait"></i></div>
  <div class="abs thumb" style="left:419px;top:822px;width:92px;height:76px"><i role="img" aria-label="Blog author portrait"></i></div>
  <div class="abs blog-card">Lorem ipsum dolor sit amet, consectetur adipisicing elit, sed do eiusmod tempor incididunt ut labore et dolore magna aliqua.<span class="date">22-12-2012</span></div>
  <div class="abs link-more" style="left:460px;top:906px">View more...</div>

  <div class="abs tech-item" style="top:738px">
    <div class="thumb"><i role="img" aria-label="Person holding a phone camera" style="background:linear-gradient(135deg,#b08870,#3a3a3a)"></i></div>
    <p>Explain to you how all this mistaken idea of denouncing pleasure Lorem ipsum dolor sit amet, consectetur adipisicing elit, sed do eiusmod tempor incididunt ut labore et dolore magna aliqua.</p>
  </div>
  <div class="abs tech-item" style="top:822px">
    <div class="thumb"><i role="img" aria-label="Hand holding a tablet showing a video" style="background:linear-gradient(135deg,#222,#6a8a70)"></i></div>
    <p>Explain to you how all this mistaken idea of denouncing pleasure Lorem ipsum dolor sit amet, consectetur adipisicing elit, sed do eiusmod tempor incididunt ut labore et dolore magna aliqua.</p>
  </div>
  <div class="abs link-more" style="left:678px;top:906px">Read more...</div>

  <div class="abs alliance">
    <h3>ALLIANCE &amp; PARTNERS</h3>
    <div class="partners">
      <span>Northwind</span><span>Wishbridge</span><span>strova</span><span>Fizzola</span><span>pixora</span><span>Blogmetrix</span><span>TrustSeal</span>
    </div>
  </div>

  <footer class="abs footer">
    <h4 style="left:75px;top:32px">Sitemap</h4>
    <ul class="sitemap"><li>Home</li><li>About Us</li><li>Press</li><li>Technology</li><li>Contact Us</li></ul>
    <h4 style="left:210px;top:34px">Follow Us On</h4>
    <div class="social"><i></i><i></i><i></i><i></i><i></i></div>
    <h4 style="left:401px;top:34px">Contact Info</h4>
    <div class="contact">#12 Lakeview Lane, Lorem ipsum,<br>P: +91 800123456 &nbsp;T: (004) 55501234<br>E-mail: info@prism48.com</div>
    <div class="map" role="img" aria-label="Street map with office location pin"></div>
    <div class="copy">© 2012.www.prism48.com</div>
  </footer>
</div>
</body>
</html>
```